Hartwell Estates Business Cards

I would like a business card that includes myself and my partner.
Includes: Logo, office #, email, website, our names, our numbers and possibly the address. I would also like the logo to be embossed and the card to be horizontal.
There is a photo of our yard signs to give you an idea of the colors of our business.

Target Market(s)

Everyone in real estate market.
We are in a rural area. Our clientele are from all socioeconomic backgrounds.

Industry/Entity Type

Real Estate Agent

Contact Information for Business Card

Company Name: Hartwell Estates
Our Names, Titles & Cell #'s : Dana Pembrook-Broker (555).317.6624, Marla Pembrook-Realtor (555).609.1385
Office #: (555).240.3918
Website: hartwellestates-demo.com
Joint Email: pembrook@hartwellestates-demo.com
Office Address: 418B W. Calloway Ave.
Fenwick, OK. 70913

Font styles to use
Serif

Requirements
Must have
• HORIZONTAL, Logo, Myself and my partners names, Our cell #'s, our office #, our website, our email address
Nice to have
• Embossed logo, office address, our titles.

```html
<!DOCTYPE html>
<html lang="en">
<head>
<meta charset="utf-8">
<title>Hartwell Estates Business Cards</title>
<link rel="stylesheet" href="https://fonts.googleapis.com/css2?family=PT+Sans:wght@400;700&display=swap">
<style>
  :root {
    --backdrop: #e6e4e8;
    --card: #ffffff;
    --purple: #4b1e6b;
    --ink: #2a2a2a;
    --muted: #555555;
  }
  * { margin: 0; padding: 0; box-sizing: border-box; }
  html, body { width: 1200px; height: 844px; overflow: hidden; }
  body {
    background: var(--backdrop);
    font-family: "PT Sans", Arial, sans-serif;
    color: var(--ink);
    display: flex;
    align-items: center;
    justify-content: center;
    gap: 40px;
  }
  .card {
    width: 540px;
    height: 309px;
    background: var(--card);
    box-shadow: 0 6px 18px rgba(0,0,0,0.18);
    position: relative;
  }
  /* Front */
  .card-front {
    padding: 30px 40px 30px 70px;
    display: flex;
    flex-direction: column;
  }
  .brand-name {
    font-family: "PT Sans", Arial, sans-serif;
    font-weight: 700;
    font-size: 30px;
    color: var(--purple);
    line-height: 1;
  }
  .agents {
    display: flex;
    gap: 34px;
    margin-top: 24px;
  }
  .agent-name {
    font-weight: 700;
    font-size: 16px;
    color: var(--purple);
    line-height: 1.2;
  }
  .agent-title { font-size: 12px; color: var(--muted); }
  .agent-phone {
    font-size: 13px;
    margin-top: 4px;
    display: flex;
    align-items: center;
    gap: 5px;
  }
  .icon { width: 11px; height: 11px; fill: var(--purple); flex: none; }
  .office {
    margin-top: 16px;
    font-size: 13px;
    display: grid;
    grid-template-columns: auto auto;
    column-gap: 22px;
    row-gap: 4px;
    justify-content: start;
  }
  .office-line { display: flex; align-items: center; gap: 5px; white-space: nowrap; }
  .address {
    margin-top: auto;
    font-size: 13px;
  }
  /* Back */
  .card-back {
    display: flex;
    align-items: center;
    justify-content: center;
  }
  .back-name {
    font-family: "PT Sans", Arial, sans-serif;
    font-weight: 700;
    font-size: 44px;
    color: var(--purple);
    text-align: center;
    line-height: 1.1;
  }
</style>
</head>
<body>
  <section class="card card-front" aria-label="Business card front">
    <div class="brand-name">Hartwell Estates</div>

    <div class="agents">
      <div class="agent">
        <div class="agent-name">Dana Pembrook</div>
        <div class="agent-title">Broker</div>
        <div class="agent-phone">
          <svg class="icon" viewBox="0 0 24 24" aria-hidden="true"><path d="M6.6 10.8a15 15 0 0 0 6.6 6.6l2.2-2.2c.3-.3.7-.4 1-.2 1.1.4 2.3.6 3.6.6.6 0 1 .4 1 1V20c0 .6-.4 1-1 1C10.6 21 3 13.4 3 4c0-.6.4-1 1-1h3.5c.6 0 1 .4 1 1 0 1.3.2 2.5.6 3.6.1.3 0 .7-.2 1z"/></svg>
          (555).317.6624
        </div>
      </div>
      <div class="agent">
        <div class="agent-name">Marla Pembrook</div>
        <div class="agent-title">Realtor</div>
        <div class="agent-phone">
          <svg class="icon" viewBox="0 0 24 24" aria-hidden="true"><path d="M6.6 10.8a15 15 0 0 0 6.6 6.6l2.2-2.2c.3-.3.7-.4 1-.2 1.1.4 2.3.6 3.6.6.6 0 1 .4 1 1V20c0 .6-.4 1-1 1C10.6 21 3 13.4 3 4c0-.6.4-1 1-1h3.5c.6 0 1 .4 1 1 0 1.3.2 2.5.6 3.6.1.3 0 .7-.2 1z"/></svg>
          (555).609.1385
        </div>
      </div>
    </div>

    <div class="office">
      <div class="office-line">
        <svg class="icon" viewBox="0 0 24 24" aria-hidden="true"><path d="M6.6 10.8a15 15 0 0 0 6.6 6.6l2.2-2.2c.3-.3.7-.4 1-.2 1.1.4 2.3.6 3.6.6.6 0 1 .4 1 1V20c0 .6-.4 1-1 1C10.6 21 3 13.4 3 4c0-.6.4-1 1-1h3.5c.6 0 1 .4 1 1 0 1.3.2 2.5.6 3.6.1.3 0 .7-.2 1z"/></svg>
        (555).240.3918
      </div>
      <div class="office-line">
        <svg class="icon" viewBox="0 0 24 24" aria-hidden="true"><path d="M2 5h20v14H2z M2 5l10 8 10-8" fill="none" stroke="#4b1e6b" stroke-width="2"/></svg>
        pembrook@hartwellestates-demo.com
      </div>
      <div></div>
      <div class="office-line">
        <svg class="icon" viewBox="0 0 24 24" aria-hidden="true"><circle cx="12" cy="12" r="9" fill="none" stroke="#4b1e6b" stroke-width="2"/><path d="M3 12h18M12 3c3 3 3 15 0 18M12 3c-3 3-3 15 0 18" fill="none" stroke="#4b1e6b" stroke-width="1.5"/></svg>
        hartwellestates-demo.com
      </div>
    </div>

    <div class="address">418B W. Calloway Ave. Fenwick, OK. 70913</div>
  </section>

  <section class="card card-back" aria-label="Business card back">
    <div class="back-name">Hartwell<br>Estates</div>
  </section>
</body>
</html>
```